Core Investment Strategy's Super Pie Chart

We need a one page visual explanation of an investment strategy we call "Keystone/Orbit". This strategy emphasizes a "core" portfolio that will seldom change and "perimeter" investments that will change. Our investment management firm caters to wealthy individuals. We want to project an image of strength and reliability. At the same time, we are willing to explore new concepts. I have uploaded a PDF of my graphically-challenged assistant's attempt at creating the one page visual.

```html
<!DOCTYPE html>
<html lang="en">
<head>
<meta charset="utf-8">
<title>Keystone / Orbit Portfolio</title>
<link rel="stylesheet" href="https://fonts.googleapis.com/css2?family=Cinzel:wght@400;500;600&display=swap">
<style>
  :root {
    --paper: #ffffff;
    --panel-light: #ececed;
    --panel-dark: #d3d3d6;
    --ink: #2f2f33;
    --green: #8dc63f;
    --green-deep: #0b6b3a;
    --orange: #fbad3f;
    --orange-deep: #f7941d;
    --tan: #c49a6c;
    --tan-deep: #5d4a3c;
    --ring-white: #ffffff;
    --ring-grey: #6d6e71;
    --blue: #1375bc;
    --blue-side: #2b3a93;
    --blue-line: #0d3f6e;
    --pink: #ef7bb0;
    --pink-side: #e5197a;
    --pink-line: #ce1a6a;
    --label-green: #0b8a46;
    --label-orange: #f26522;
    --label-brown: #6b4a2f;
    --label-blue: #1375bc;
    --label-pink: #e5197a;
  }
  html, body {
    margin: 0;
    width: 1200px;
    height: 900px;
    overflow: hidden;
    background: var(--paper);
    font-family: "Cinzel", "Times New Roman", serif;
  }
  .canvas { position: relative; width: 1200px; height: 900px; }
  .panel {
    position: absolute; left: 37px; top: 167px; width: 1151px; height: 646px;
    background: radial-gradient(ellipse at 50% 45%, var(--panel-light) 0%, #e2e2e4 55%, var(--panel-dark) 100%);
  }
  .title {
    position: absolute; left: 0; width: 1200px; top: 176px; margin: 0;
    text-align: center; font-weight: 400; font-size: 38px; letter-spacing: 1px;
    color: var(--ink);
  }
  .chart { position: absolute; left: 0; top: 0; }
  .label { position: absolute; margin: 0; line-height: 1.15; white-space: nowrap; }
  .label--core { left: 292px; top: 274px; font-size: 15px; color: var(--label-green); }
  .label--alt { left: 830px; top: 279px; font-size: 15px; color: var(--label-orange); }
  .label--other { left: 328px; top: 678px; font-size: 26px; color: var(--ink); }
  .label--funds { left: 866px; top: 667px; font-size: 13px; color: var(--label-brown); }
  .label--bond { font-size: 19px; color: var(--label-pink); right: 888px; }
  .label--short { top: 490px; }
  .label--inter { top: 518px; }
  .label--equity { left: 938px; font-size: 18px; color: var(--label-blue); }
  .label--lg { top: 467px; }
  .label--mid { top: 501px; }
  .label--sm { top: 534px; }
  .label--intl { top: 569px; }
</style>
</head>
<body>
<main class="canvas">
  <div class="panel"></div>
  <h1 class="title">Keystone / Orbit Portfolio</h1>

  <svg class="chart" width="1200" height="900" viewBox="0 0 1200 900" aria-label="Portfolio allocation chart">
    <!-- outer ring shadows -->
    <g class="ring-shadow" fill="none" stroke-width="26">
      <path d="M873 506 A245 245 0 0 1 631 748" stroke="var(--tan-deep)"/>
      <path d="M625 748 A245 245 0 0 1 383 506" stroke="var(--ring-grey)"/>
    </g>
    <!-- outer ring -->
    <g class="ring" fill="none" stroke-width="26">
      <path d="M383 490 A245 245 0 0 1 625 248" stroke="var(--green)"/>
      <path d="M631 248 A245 245 0 0 1 873 490" stroke="var(--orange)"/>
      <path d="M873 496 A245 245 0 0 1 631 738" stroke="var(--tan)"/>
      <path d="M625 738 A245 245 0 0 1 383 496" stroke="var(--ring-white)"/>
    </g>
    <g class="ring-inner" fill="none" stroke-width="8">
      <path d="M397 490 A231 231 0 0 1 625 262" stroke="var(--green-deep)"/>
      <path d="M631 262 A231 231 0 0 1 859 490" stroke="var(--orange-deep)"/>
    </g>

    <!-- pie sides (depth) -->
    <g class="pie-side" transform="translate(0 14)">
      <path d="M628 323 A170 170 0 0 1 741.8 619.3 L649.4 516.8 A32 32 0 0 0 628 461 Z" fill="var(--blue-side)"/>
      <path d="M741.8 619.3 A170 170 0 0 1 705.2 644.5 L642.5 521.5 A32 32 0 0 0 649.4 516.8 Z" fill="var(--blue-side)"/>
      <path d="M705.2 644.5 A170 170 0 0 1 663.4 659.3 L634.7 524.3 A32 32 0 0 0 642.5 521.5 Z" fill="var(--blue-side)"/>
      <path d="M663.4 659.3 A170 170 0 0 1 556.1 647 L614.5 522 A32 32 0 0 0 634.7 524.3 Z" fill="var(--blue-side)"/>
      <path d="M556.1 647 A170 170 0 0 1 514.2 366.7 L606.6 469.2 A32 32 0 0 0 614.5 522 Z" fill="var(--pink-side)"/>
      <path d="M514.2 366.7 A170 170 0 0 1 628 323 L628 461 A32 32 0 0 0 606.6 469.2 Z" fill="var(--pink-side)"/>
    </g>
    <!-- pie tops -->
    <g class="pie-top" stroke-width="2">
      <path d="M628 323 A170 170 0 0 1 741.8 619.3 L649.4 516.8 A32 32 0 0 0 628 461 Z" fill="var(--blue)" stroke="var(--blue-line)"/>
      <path d="M741.8 619.3 A170 170 0 0 1 705.2 644.5 L642.5 521.5 A32 32 0 0 0 649.4 516.8 Z" fill="var(--blue)" stroke="var(--blue-line)"/>
      <path d="M705.2 644.5 A170 170 0 0 1 663.4 659.3 L634.7 524.3 A32 32 0 0 0 642.5 521.5 Z" fill="var(--blue)" stroke="var(--blue-line)"/>
      <path d="M663.4 659.3 A170 170 0 0 1 556.1 647 L614.5 522 A32 32 0 0 0 634.7 524.3 Z" fill="var(--blue)" stroke="var(--blue-line)"/>
      <path d="M556.1 647 A170 170 0 0 1 514.2 366.7 L606.6 469.2 A32 32 0 0 0 614.5 522 Z" fill="var(--pink)" stroke="var(--pink-line)"/>
      <path d="M514.2 366.7 A170 170 0 0 1 628 323 L628 461 A32 32 0 0 0 606.6 469.2 Z" fill="var(--pink)" stroke="var(--pink-line)"/>
    </g>
    <line x1="628" y1="323" x2="628" y2="461" stroke="var(--paper)" stroke-width="4"/>

    <!-- connectors -->
    <g class="connector connector--pink" fill="none" stroke="var(--pink)" stroke-width="2.5">
      <polyline points="525,360 430,360 430,503 352,503"/>
      <polyline points="462,530 352,530"/>
    </g>
    <g class="arrow arrow--pink" fill="var(--pink)">
      <polygon points="332,503 342,495 356,495 356,511 342,511"/>
      <polygon points="332,530 342,522 356,522 356,538 342,538"/>
    </g>
    <g class="connector connector--blue" fill="none" stroke="var(--blue)" stroke-width="2.5">
      <polyline points="790,478 906,478"/>
      <polyline points="738,615 796,615 796,512 906,512"/>
      <polyline points="712,645 830,645 830,545 906,545"/>
      <polyline points="605,658 605,705 852,705 852,580 906,580"/>
    </g>
    <g class="arrow arrow--blue" fill="var(--blue)">
      <polygon points="904,470 918,470 928,478 918,486 904,486"/>
      <polygon points="904,504 918,504 928,512 918,520 904,520"/>
      <polygon points="904,537 918,537 928,545 918,553 904,553"/>
      <polygon points="904,572 918,572 928,580 918,588 904,588"/>
    </g>
  </svg>

  <p class="label label--core">Attractive Core<br>Assets,</p>
  <p class="label label--alt">Alternative Assets</p>
  <p class="label label--other">Other</p>
  <p class="label label--funds">Actively Managed<br>Mutual Funds</p>

  <p class="label label--bond label--short">Short Term Bonds</p>
  <p class="label label--bond label--inter">Intermediate Bonds</p>

  <p class="label label--equity label--lg">Lg. Cap Equities</p>
  <p class="label label--equity label--mid">Mid Cap Equities</p>
  <p class="label label--equity label--sm">Sm Cap Equities</p>
  <p class="label label--equity label--intl">Int'l/dev Cap Equities</p>
</main>
</body>
</html>
```